Small Business Broker Business Card Design

A business card design for a small business brokerage, which is a financial service, not unlike real estate brokerage, but for small businesses such as laundromats, pizza shops, restaurants, cleaners etc. The designs should all be simple, more conservative in nature, using the colors and font of the logo. Again, think real estate Brokerage as a business context
Contact Information for Business Card
Name: Glen R. Harlow. Title: Small Business Advisor. Email: g.harlow@bayfieldcapitalworks.example. Mobile: (555) 274-3918. Office: (555) 806-2147. www.bayfieldcapitalworks.example

```html
<!DOCTYPE html>
<html lang="en">
<head>
<meta charset="utf-8">
<title>Bayfield Capital Works – Business Card</title>
<link rel="stylesheet" href="https://fonts.googleapis.com/css2?family=Josefin+Sans:wght@700&family=Montserrat:wght@400;600&display=swap">
<style>
  :root {
    --navy: #1b396a;
    --white: #ffffff;
    --ink: #1f1f1f;
    --backdrop: #9a9a9a;
  }
  * { box-sizing: border-box; margin: 0; padding: 0; }
  html, body { width: 1093px; height: 1200px; overflow: hidden; }
  body { background: var(--backdrop); position: relative; font-family: "Montserrat", sans-serif; }

  .card { position: absolute; left: 264px; width: 582px; height: 364px; }
  .card--front { top: 225px; background: var(--white); }
  .card--back { top: 615px; background: var(--navy); }

  .mark-square { position: absolute; }
  .card--front .mark-square { left: 120px; top: 126px; width: 76px; height: 76px; background: var(--navy); }
  .card--back .mark-square { left: 248px; top: 104px; width: 84px; height: 84px; background: var(--white); }

  .divider { position: absolute; left: 269px; top: 99px; width: 1.5px; height: 146px; background: var(--navy); }

  .contact { position: absolute; left: 280px; top: 98px; }
  .contact__name { font-family: "Josefin Sans", sans-serif; font-weight: 700; font-size: 23px; color: var(--navy); line-height: 1; padding-top: 4px; }
  .contact__title { font-size: 12.5px; color: var(--ink); margin-top: 4px; }
  .contact__list { list-style: none; margin-top: 17px; }
  .contact__list li { font-size: 12.5px; color: var(--ink); height: 25px; white-space: nowrap; }
  .contact__label { font-weight: 600; color: var(--navy); display: inline-block; width: 20px; }

  .brand { position: absolute; left: 0; width: 100%; text-align: center; }
  .card--front .brand { top: 292px; }
  .card--back .brand { top: 234px; }
  .brand__name { font-family: "Josefin Sans", sans-serif; font-weight: 700; font-size: 25px; color: var(--navy); line-height: 1; letter-spacing: 0.3px; }
  .card--back .brand__name { color: var(--white); }
</style>
</head>
<body>
  <section class="card card--front">
    <div class="mark-square" aria-hidden="true"></div>
    <div class="divider"></div>
    <div class="contact">
      <h1 class="contact__name">GLEN R. HARLOW</h1>
      <p class="contact__title">Small Business Advisor</p>
      <ul class="contact__list">
        <li><span class="contact__label">M:</span>(555) 274-3918</li>
        <li><span class="contact__label">O:</span>(555) 806-2147</li>
        <li><span class="contact__label">E:</span>g.harlow@bayfieldcapitalworks.example</li>
        <li><span class="contact__label">W:</span>www.bayfieldcapitalworks.example</li>
      </ul>
    </div>
    <div class="brand">
      <p class="brand__name">BAYFIELD CAPITAL WORKS, INC</p>
    </div>
  </section>

  <section class="card card--back">
    <div class="mark-square" aria-hidden="true"></div>
    <div class="brand">
      <p class="brand__name">BAYFIELD CAPITAL WORKS, INC</p>
    </div>
  </section>
</body>
</html>
```